Business card design Needed for new logo / Construction business, home extensions and new builds

We need a business card design using our new logo files which i will attach to this project :)

We are a small construction business specialising in home extensions, new builds and property development. We are very ambitious and would appreciate professional and elegant designs for our new business card.

Very serious about using the services on MakerQuarry and recently acquired our new logo from here :)

Please get involved, i will feedback when i can as i am very busy but can respond daily, thanks

Target Market(s)

People that want to build onto their houses, new building developments or adding too their existing property

Industry/Entity Type

Construction

Contact Information for Business Card

Renwick Tolliver Construction, Lionel Ashby (Managing Director), Tel 07822254961, email - info@renwick-tolliver, www.renwick-tolliver.co.uk

Colors

Designer to choose colors to be used in the design.

Requirements
Must have
• I like a deep grey on the back please. A lot of you have provided black from and back, try mixing things up a little. The black looks cool 😎 Thanks

```html
<!DOCTYPE html>
<html lang="en">
<head>
<meta charset="utf-8">
<title>Renwick Tolliver Construction – Business Card</title>
<link href="https://fonts.googleapis.com/css2?family=Open+Sans:wght@400;600;700&display=swap" rel="stylesheet">
<style>
  :root {
    --backdrop: #2a2a2d;
    --card-front: #1f1f23;
    --card-back: #2b2b2f;
    --silver: #d4d5d8;
    --text-light: #e6e6e8;
    --gold: #d9a227;
    --divider: #8d8e93;
    --back-mark: #3b3b40;
  }
  * { margin: 0; padding: 0; box-sizing: border-box; }
  html, body { width: 1200px; height: 780px; overflow: hidden; }
  body {
    background: var(--backdrop);
    font-family: "Open Sans", sans-serif;
    position: relative;
  }
  .card {
    position: absolute;
    top: 235px;
    width: 540px;
    height: 310px;
    border-radius: 4px;
    overflow: hidden;
    box-shadow: 0 10px 28px rgba(0,0,0,.45);
  }
  .card--front { left: 40px; background: var(--card-front); }
  .card--back  { left: 620px; background: var(--card-back); }

  .brand {
    position: absolute;
    display: flex;
    align-items: center;
    gap: 10px;
  }
  .brand__square {
    width: 14px; height: 14px;
    background: var(--gold);
    flex: none;
  }
  .brand__name {
    font-weight: 600;
    font-size: 15px;
    letter-spacing: 1.5px;
    line-height: 1.35;
    text-transform: uppercase;
    color: var(--gold);
  }
  .card--front .brand { left: 34px; top: 112px; width: 210px; }

  .divider {
    position: absolute;
    left: 0; top: 0;
  }

  .contact {
    position: absolute;
    left: 296px;
    top: 98px;
    color: var(--text-light);
  }
  .contact__name {
    font-weight: 700;
    font-size: 27px;
    line-height: 1.1;
    color: var(--silver);
  }
  .contact__name .surname { color: var(--gold); }
  .contact__role {
    font-size: 13px;
    margin-top: 4px;
  }
  .contact__address {
    font-size: 13px;
    line-height: 1.45;
    margin-top: 12px;
  }
  .contact__lines {
    list-style: none;
    margin-top: 10px;
    font-size: 13px;
    line-height: 1.65;
  }
  .contact__lines li { display: flex; align-items: center; gap: 8px; }
  .contact__lines svg { width: 12px; height: 12px; flex: none; }
  .contact__lines .no-icon { padding-left: 20px; }

  .card--back .brand {
    left: 0; right: 0; top: 0; bottom: 0;
    justify-content: center;
  }
  .card--back .brand__square { background: var(--back-mark); width: 18px; height: 18px; }
  .card--back .brand__name { color: var(--back-mark); font-size: 19px; letter-spacing: 2px; }
</style>
</head>
<body>

<section class="card card--front" aria-label="Business card front">
  <div class="brand">
    <span class="brand__square"></span>
    <span class="brand__name">Renwick Tolliver Construction</span>
  </div>

  <svg class="divider" width="540" height="310" aria-hidden="true">
    <line x1="278" y1="70" x2="246" y2="262" stroke="var(--divider)" stroke-width="1"/>
  </svg>

  <div class="contact">
    <p class="contact__name">Lionel <span class="surname">Ashby</span></p>
    <p class="contact__role">Managing Director</p>
    <p class="contact__address">Hallow Lane, Westcombe<br>Thornbury, TB4 7QK</p>
    <ul class="contact__lines">
      <li>
        <svg viewBox="0 0 24 24" aria-hidden="true"><path fill="var(--gold)" d="M6.6 10.8a15.1 15.1 0 0 0 6.6 6.6l2.2-2.2a1 1 0 0 1 1-.25 11.4 11.4 0 0 0 3.6.57 1 1 0 0 1 1 1V20a1 1 0 0 1-1 1A17 17 0 0 1 3 4a1 1 0 0 1 1-1h3.5a1 1 0 0 1 1 1c0 1.25.2 2.45.57 3.57a1 1 0 0 1-.25 1z"/></svg>
        0782 225 4961
      </li>
      <li>
        <svg viewBox="0 0 24 24" aria-hidden="true"><rect x="2" y="5" width="20" height="14" rx="1.5" fill="var(--gold)"/><path d="M3 6l9 7 9-7" fill="none" stroke="var(--card-front)" stroke-width="1.8"/></svg>
        info@renwick-tolliver.co.uk
      </li>
      <li>
        <svg viewBox="0 0 24 24" aria-hidden="true"><circle cx="12" cy="12" r="9.5" fill="none" stroke="var(--gold)" stroke-width="2"/><path d="M2.5 12h19M12 2.5c3 3 3 16 0 19M12 2.5c-3 3-3 16 0 19" fill="none" stroke="var(--gold)" stroke-width="1.6"/></svg>
        www.renwick-tolliver.co.uk
      </li>
    </ul>
  </div>
</section>

<section class="card card--back" aria-label="Business card back">
  <div class="brand">
    <span class="brand__square"></span>
    <span class="brand__name">Renwick Tolliver<br>Construction</span>
  </div>
</section>

</body>
</html>
```